Dental specialist needs a sharp looking letterhead

I am looking for a letterhead to be used to send letters and communication between myself (a dental specialist) and other dentists.
My office is a state of the art dental specialty office.
I need to letterhead to also state:
Bertram L. Oswick DDS
2748 Tollard Avenue, Suite K
West Tollard, NY 14391
(716)392-5061
fax: (716)392-5087
oswickroot.com (**this email address may change)

i included my logo designs.
thank you

Target Market(s)

dentists

Industry/Entity Type

Communication

Requirements
Must have
• the included logo, whether the vertical or horizontal versions

```html
<!DOCTYPE html>
<html lang="en">
<head>
<meta charset="utf-8">
<title>Keystone Endodontics Letterhead</title>
<link rel="stylesheet" href="https://fonts.googleapis.com/css2?family=Didact+Gothic&family=Questrial&display=swap">
<style>
  :root {
    --bg: #ececec;
    --paper: #ffffff;
    --ink: #2e2e2e;
    --ink-soft: #555555;
    --brand-blue: #1e9be0;
    --brand-green: #7cbf3c;
    --sig-ink: #3d56a8;
  }
  * { box-sizing: border-box; margin: 0; padding: 0; }
  html, body {
    width: 1200px; height: 936px; overflow: hidden;
    background: var(--bg);
    font-family: "Didact Gothic", "Questrial", sans-serif;
    color: var(--ink);
  }
  .letterhead {
    position: absolute; left: 289px; top: 28px;
    width: 622px; height: 880px;
    background: var(--paper);
    box-shadow: 0 2px 10px rgba(0,0,0,.12);
    overflow: hidden;
  }
  .brand {
    position: absolute; left: 52px; top: 70px;
    display: flex; align-items: center; gap: 10px;
  }
  .brand-dot {
    width: 26px; height: 26px; border-radius: 50%;
    background: var(--brand-blue);
  }
  .brand-name {
    font-size: 15px; letter-spacing: .06em; color: var(--ink);
    text-transform: uppercase;
  }
  .contact {
    position: absolute; right: 52px; top: 58px;
    font-size: 8.5px; line-height: 1.55; color: var(--ink-soft);
  }
  .contact-name { font-weight: 700; color: var(--ink); font-size: 9.5px; margin-bottom: 2px; letter-spacing: .03em; }
  .contact-row { display: flex; align-items: center; gap: 5px; }
  .contact-icon { width: 9px; height: 9px; flex: none; }
  .contact-address { padding-left: 14px; margin-top: 2px; }
  .letter-body {
    position: absolute; left: 52px; top: 232px; width: 500px;
    font-size: 10.5px; line-height: 1.6; color: var(--ink-soft);
  }
  .salutation { font-weight: 700; color: var(--ink); font-size: 12.5px; margin-bottom: 12px; }
  .letter-body p { margin-bottom: 14px; }
  .closing { margin-top: 10px; display: flex; align-items: flex-end; gap: 18px; }
  .closing-text { font-size: 10.5px; }
  .signer { font-weight: 700; font-size: 12.5px; color: var(--ink); }
  .signature {
    width: 110px; height: 46px; border-radius: 4px;
    background: linear-gradient(135deg, rgba(61,86,168,.18), rgba(61,86,168,.06));
  }
  .footer-swoosh { position: absolute; inset: 0; pointer-events: none; }
</style>
</head>
<body>
  <main class="letterhead">
    <div class="brand">
      <span class="brand-dot"></span>
      <span class="brand-name">Keystone Endodontics P.C.</span>
    </div>

    <address class="contact">
      <div class="contact-name">BERTRAM L. OSWICK DDS</div>
      <div class="contact-row">
        <svg class="contact-icon" viewBox="0 0 10 10"><circle cx="5" cy="5" r="5" fill="var(--brand-blue)"/><path d="M3.2 2.6l1 1-.5.7a3.5 3.5 0 0 0 2 2l.7-.5 1 1-.8.8C4.9 7.4 2.6 5.1 2.4 3.4z" fill="#fff"/></svg>
        <span>(716)392-5061</span>
      </div>
      <div class="contact-row">
        <svg class="contact-icon" viewBox="0 0 10 10"><circle cx="5" cy="5" r="5" fill="var(--brand-blue)"/><rect x="3" y="3.8" width="4" height="3" fill="#fff"/><rect x="3.6" y="2.6" width="2.8" height="1.4" fill="#fff"/></svg>
        <span>(716)392-5087</span>
      </div>
      <div class="contact-row">
        <svg class="contact-icon" viewBox="0 0 10 10"><circle cx="5" cy="5" r="5" fill="var(--brand-blue)"/><rect x="2.6" y="3.2" width="4.8" height="3.6" fill="#fff"/><path d="M2.6 3.2L5 5.2 7.4 3.2" stroke="var(--brand-blue)" stroke-width=".6" fill="none"/></svg>
        <span>info@oswickroot.com</span>
      </div>
      <div class="contact-row">
        <svg class="contact-icon" viewBox="0 0 10 10"><circle cx="5" cy="5" r="5" fill="var(--brand-blue)"/><circle cx="5" cy="5" r="2.4" fill="none" stroke="#fff" stroke-width=".7"/><path d="M2.6 5h4.8M5 2.6v4.8" stroke="#fff" stroke-width=".6"/></svg>
        <span>www.oswickroot.com</span>
      </div>
      <div class="contact-row">
        <svg class="contact-icon" viewBox="0 0 10 10"><circle cx="5" cy="5" r="5" fill="var(--brand-blue)"/><path d="M5 2.3a1.8 1.8 0 0 1 1.8 1.8C6.8 5.4 5 7.6 5 7.6S3.2 5.4 3.2 4.1A1.8 1.8 0 0 1 5 2.3z" fill="#fff"/></svg>
        <span>2748 Tollard Avenue, Suite K</span>
      </div>
      <div class="contact-address">West Tollard, NY 14391</div>
    </address>

    <section class="letter-body">
      <div class="salutation">Dear sir / madame,</div>
      <p>Lorem ipsum dolor sit amet, consectetur adipisicing elit, sed do eiusmod tempor incididunt ut labore et dolore magna aliqua. Ut enim ad minim veniam, quis nostrud exercitation ullamco laboris nisi ut aliquip ex ea commodo consequat. Duis aute irure dolor in reprehenderit in voluptate velit esse cillum dolore eu fugiat nulla pariatur. Excepteur sint occaecat cupidatat non proident, sunt in culpa qui officia deserunt mollit anim id est laborum.Lorem ipsum dolor sit amet, consectetur adipisicing elit, sed do eiusmod tempor incididunt ut labore et dolore magna aliqua. Ut enim ad minim veniam, quis nostrud exercitation ullamco laboris nisi ut aliquip ex ea commodo consequat. Duis aute irure dolor in reprehenderit in voluptate velit esse cillum dolore eu fugiat nulla pariatur. Excepteur sint occaecat cupidatat non proident, sunt in culpa qui officia deserunt mollit anim id est laborum.</p>
      <p>Lorem ipsum dolor sit amet, consectetur adipisicing elit, sed do eiusmod tempor incididunt ut labore et dolore magna aliqua. Ut enim ad minim veniam, quis nostrud exercitation ullamco laboris nisi ut aliquip ex ea commodo consequat. Duis aute irure dolor in reprehenderit in voluptate velit esse cillum dolore eu fugiat nulla pariatur. Excepteur sint occaecat cupidatat non proident, sunt in culpa qui officia deserunt mollit anim id est laborum.</p>
      <div class="closing">
        <div class="closing-text">
          Yours Sincerely,<br>
          <span class="signer">Lorna Pavick</span>
        </div>
        <div class="signature" role="img" aria-label="Handwritten signature of the sender"></div>
      </div>
    </section>

    <svg class="footer-swoosh" viewBox="0 0 622 880" aria-hidden="true">
      <path d="M622 560 L622 588 C540 680 470 780 412 880 L380 880 C450 770 540 660 622 560Z" fill="var(--brand-blue)"/>
      <path d="M0 880 L0 875 C140 862 300 838 410 780 C340 836 200 868 70 880Z" fill="var(--brand-green)"/>
    </svg>
  </main>
</body>
</html>
```